Computer consultant business card

Bexil Software is a newly started computer consulting company. It's a small one-man company that provides mostly Vornix applications but also websites in collaboration with designers. I'm running this company on the side of full time university studies.

I want the final design to be clean and memorable. Be creative! :)

Some inspiration:
http://www.pixelmarta.com/design/48317
http://www.pixelmarta.com/design/2739164/business-card-design-by-frostlynk
http://www.pixelmarta.com/design/604281/business-card-design-by-koralind-vestrabanu

See attachment for my company logo.
Updates

I would like to thank everyone for submitting! I'll need a couple of days to review and ultimately select a design.

Target Market(s)

Non-technical entrepreneurs and small companies.

Industry/Entity Type

University

Requirements
Must have
• My company logo.
In any way, both colors from my logo.
First- and last name, e-mail and phone number.
Double-sided design.
Nice to have
• Something creative with the symbol in my logo

```html
<!DOCTYPE html>
<html lang="en">
<head>
<meta charset="utf-8">
<title>Qelvo – Business Card</title>
<link rel="stylesheet" href="https://fonts.googleapis.com/css2?family=Exo+2:wght@500;600&family=Open+Sans:wght@400&display=swap">
<style>
  :root {
    --backdrop: #2b2b2b;
    --card-light: #f4f4f4;
    --card-mid: #e2e2e2;
    --card-shade: #d2d2d2;
    --ink-dark: #2d2d2d;
    --ink-body: #3a3a3a;
    --brand-blue: #3b6fc0;
    --pattern-tone: #d9d9d9;
  }
  * { box-sizing: border-box; margin: 0; padding: 0; }
  html, body {
    width: 1200px; height: 900px; overflow: hidden;
    background: var(--backdrop);
  }
  .canvas { position: relative; width: 1200px; height: 900px; }

  .card {
    position: absolute;
    width: 525px; height: 300px;
    border-radius: 2px;
    overflow: hidden;
    box-shadow: 0 14px 30px rgba(0,0,0,.55);
  }

  /* Front card */
  .card--front {
    left: 110px; top: 110px;
    background: linear-gradient(120deg, var(--card-mid) 0%, var(--card-light) 45%, var(--card-shade) 100%);
  }
  .card--front .brand {
    position: absolute; left: 48px; bottom: 62px;
    display: flex; align-items: center; gap: 12px;
  }
  .brand__dot {
    width: 34px; height: 34px; border-radius: 50%;
    background: var(--brand-blue);
    flex: none;
  }
  .brand__name {
    font-family: "Exo 2", sans-serif; font-weight: 600;
    font-size: 44px; color: var(--ink-dark); letter-spacing: .5px;
    line-height: 1;
  }
  .contact {
    position: absolute; left: 300px; top: 58px;
    padding-left: 18px;
    border-left: 1px solid var(--brand-blue);
    height: 140px;
  }
  .contact__name {
    font-family: "Exo 2", sans-serif; font-weight: 500;
    font-size: 22px; color: var(--brand-blue); letter-spacing: 1px;
  }
  .contact__role {
    font-family: "Open Sans", sans-serif; font-size: 12px;
    color: var(--ink-body); margin-top: 2px;
  }
  .contact__list { list-style: none; margin-top: 16px; }
  .contact__item {
    display: flex; align-items: center; gap: 8px;
    font-family: "Open Sans", sans-serif; font-size: 12px;
    color: var(--ink-body); margin-bottom: 6px;
  }
  .contact__icon { width: 12px; height: 12px; flex: none; }

  /* Back card */
  .card--back {
    left: 560px; top: 470px;
    background: var(--card-light);
  }
  .card__pattern {
    position: absolute; inset: 0;
    background: linear-gradient(135deg, var(--pattern-tone) 0%, var(--card-light) 55%, var(--pattern-tone) 100%);
  }
  .card--back .brand-block {
    position: absolute; left: 120px; top: 110px;
  }
  .brand-block .brand-row { display: flex; align-items: center; gap: 16px; }
  .brand-block .brand__dot { width: 56px; height: 56px; }
  .brand-block .brand__name { font-size: 68px; }
  .brand-block__url {
    font-family: "Exo 2", sans-serif; font-weight: 500;
    font-size: 16px; color: var(--brand-blue);
    letter-spacing: 3.5px; margin: 4px 0 0 72px;
  }
</style>
</head>
<body>
<main class="canvas">

  <section class="card card--front" aria-label="Business card front">
    <div class="brand">
      <span class="brand__dot"></span>
      <span class="brand__name">qelvo</span>
    </div>
    <div class="contact">
      <h1 class="contact__name">JOHNNY DOE</h1>
      <p class="contact__role">Managing Director</p>
      <ul class="contact__list">
        <li class="contact__item">
          <svg class="contact__icon" viewBox="0 0 12 12" aria-hidden="true">
            <rect x="3" y="0.5" width="6" height="11" rx="1.2" fill="var(--brand-blue)"/>
            <rect x="4" y="2" width="4" height="6" fill="#fff"/>
          </svg>
          + (00) 1 23 987 6402
        </li>
        <li class="contact__item">
          <svg class="contact__icon" viewBox="0 0 12 12" aria-hidden="true">
            <rect x="0.5" y="2.5" width="11" height="7" fill="var(--brand-blue)"/>
            <polyline points="0.5,2.5 6,7 11.5,2.5" fill="none" stroke="#fff" stroke-width="1"/>
          </svg>
          johnny@qelvo.com.au
        </li>
      </ul>
    </div>
  </section>

  <section class="card card--back" aria-label="Business card back">
    <div class="card__pattern" role="img" aria-label="Faint repeating pattern of rounded symbols in light grey"></div>
    <div class="brand-block">
      <div class="brand-row">
        <span class="brand__dot"></span>
        <span class="brand__name">qelvo</span>
      </div>
      <p class="brand-block__url">www.qelvo.com.au</p>
    </div>
  </section>

</main>
</body>
</html>
```